Moravel Aesthetic Doctor

I require an elegant, luxurious looking business card for my aesthetic business. I am a doctor and that will set me aside from competitors. I am planning to provide home and spa based treatments to clients with high expectations. I have attached my logo.

```html
<!DOCTYPE html>
<html lang="en">
<head>
<meta charset="utf-8">
<title>Moravel Aesthetic Doctor – Business Card</title>
<link rel="stylesheet" href="https://fonts.googleapis.com/css2?family=Lato:wght@400&family=Montserrat:wght@400;500&display=swap">
<style>
  :root {
    --backdrop: #dcdde1;
    --card: #ffffff;
    --brand-blue: #3a8fd6;
    --accent-blue: #4aa3e0;
    --ink-grey: #5c5f64;
    --text-grey: #4a4d52;
  }
  * { margin: 0; padding: 0; box-sizing: border-box; }
  html, body {
    width: 1200px; height: 800px; overflow: hidden;
    background: var(--backdrop);
  }
  .canvas { position: relative; width: 1200px; height: 800px; }
  .card {
    position: absolute; left: 389px; width: 461px; height: 263px;
    background: var(--card);
  }
  .card--front { top: 93px; }
  .card--back { top: 422px; }

  .wordmark {
    position: absolute; display: flex; align-items: center;
    font-family: "Lato", sans-serif; font-weight: 400;
    color: var(--brand-blue); text-transform: uppercase;
  }
  .wordmark__dot {
    border-radius: 50%; border: 2px solid var(--brand-blue); flex: none;
  }
  .wordmark__text { line-height: 1.05; }
  .wordmark__name { display: block; }
  .wordmark__role { display: block; }

  .card--front .wordmark { left: 88px; top: 72px; gap: 16px; }
  .card--front .wordmark__dot { width: 64px; height: 64px; }
  .card--front .wordmark__name { font-size: 40px; letter-spacing: 2px; }
  .card--front .wordmark__role { font-size: 16px; letter-spacing: 3.2px; margin-top: 4px; }

  .tagline {
    position: absolute; left: 0; right: 0; top: 210px; text-align: center;
    font-family: "Lato", sans-serif; font-size: 17px; color: var(--ink-grey);
  }

  .card--back .wordmark { left: 38px; top: 105px; gap: 9px; }
  .card--back .wordmark__dot { width: 44px; height: 44px; }
  .card--back .wordmark__name { font-size: 23px; letter-spacing: 1.2px; }
  .card--back .wordmark__role { font-size: 9.6px; letter-spacing: 1.8px; margin-top: 3px; }

  .divider {
    position: absolute; left: 237px; top: 85px; width: 1px; height: 92px;
    background: var(--accent-blue);
  }
  .contact {
    position: absolute; left: 251px; top: 82px;
    font-family: "Montserrat", sans-serif; color: var(--text-grey);
  }
  .contact__name { font-size: 12.5px; font-weight: 500; color: var(--brand-blue); }
  .contact__letters { font-size: 7px; color: var(--text-grey); margin-left: 3px; }
  .contact__credential { font-size: 11px; line-height: 13.5px; margin-top: 4px; }
  .contact__list { list-style: none; margin-top: 12px; font-size: 11px; }
  .contact__list li { display: flex; align-items: center; gap: 6px; height: 14px; }
  .contact__list svg { width: 8px; height: 8px; flex: none; }
  .social { display: inline-flex; gap: 6px; margin-left: 14px; }
  .social span { width: 8px; height: 8px; border-radius: 50%; background: var(--brand-blue); }

  .services {
    position: absolute; left: 0; right: 0; top: 231px; text-align: center;
    font-family: "Lato", sans-serif; font-size: 10.6px; color: var(--ink-grey);
  }
</style>
</head>
<body>
<main class="canvas">
  <section class="card card--front">
    <div class="wordmark">
      <span class="wordmark__dot"></span>
      <span class="wordmark__text">
        <span class="wordmark__name">Moravel</span>
        <span class="wordmark__role">Aesthetic Doctor</span>
      </span>
    </div>
    <p class="tagline">Home and Spa Based Treatments</p>
  </section>

  <section class="card card--back">
    <div class="wordmark">
      <span class="wordmark__dot"></span>
      <span class="wordmark__text">
        <span class="wordmark__name">Moravel</span>
        <span class="wordmark__role">Aesthetic Doctor</span>
      </span>
    </div>
    <div class="divider"></div>
    <div class="contact">
      <p class="contact__name">Dr Elise Varden<span class="contact__letters">MRCPCH MD</span></p>
      <p class="contact__credential">Australasian Diploma<br>of Aesthetic Medicine</p>
      <ul class="contact__list">
        <li>
          <svg viewBox="0 0 10 10" aria-hidden="true"><path d="M2 0.5 L3.8 2.8 L2.9 4 Q4 6.2 6 7.1 L7.2 6.2 L9.5 8 L8.2 9.5 Q3.5 9 0.5 1.8 Z" fill="var(--brand-blue)"/></svg>
          0800 555 019
        </li>
        <li>
          <svg viewBox="0 0 10 10" aria-hidden="true"><rect x="0.5" y="2" width="9" height="6.5" fill="var(--brand-blue)"/><path d="M0.5 2 L5 5.6 L9.5 2" stroke="#fff" stroke-width="0.9" fill="none"/></svg>
          elise@moravel.co.nz
        </li>
        <li>
          <svg viewBox="0 0 10 10" aria-hidden="true"><g fill="none" stroke="var(--ink-grey)" stroke-width="0.8"><circle cx="5" cy="5" r="4.3"/><ellipse cx="5" cy="5" rx="1.9" ry="4.3"/><path d="M0.7 5 H9.3 M1.4 2.8 H8.6 M1.4 7.2 H8.6"/></g></svg>
          www.moravel.co.nz
          <span class="social"><span></span><span></span></span>
        </li>
      </ul>
    </div>
    <p class="services">Dermal injectables - Plasma facials - Microneedling Skin boosters - Excessive sweating</p>
  </section>
</main>
</body>
</html>
```